sydney wedding photography business needs a business card design

we need a business card design for a sydney based wedding photography and videography business. our business name is :golden hour studio and film. our target clients are 24-35 yrs female. our style is candid, organic, natural, dynamic. we are a team of young photographers and videographers, and help brides to create memories that they will cherish for the rest of their lives. the logo will be provided. we want an elegant design that reflects our style, and also want to give a great impression to our clients that we are one of the best studios in sydney and our brand means quality and premium service.

Target Market(s)

bride to be, 24-35 years old, living in sydney and surrunding areas

Industry/Entity Type

Wedding Photography

Contact Information for Business Card

address: 57 tarrant street, glenmore nsw 2047
mobile: 0431872259
phone: (02) 9163 2408
info@tidewillowstudio.net.au
www.tidewillowstudio.net.au
facebook:tidewillowweddings
instagram:tidewillowweddings

Font styles to use
Serif
Sans Serif

Requirements
Nice to have
• maybe add my slogan"love stories kept forever" if the layout looks good
Should not have
• no black color, not good idea for wedding biz card

```html
<!DOCTYPE html>
<html lang="en">
<head>
<meta charset="utf-8">
<title>Golden Hour Studio and Film – Business Card</title>
<link rel="stylesheet" href="https://fonts.googleapis.com/css2?family=Montserrat:wght@400;600;800&family=Open+Sans:wght@400;600&display=swap">
<style>
  :root {
    --navy: #0f3470;
    --navy-deep: #0a2656;
    --gold: #e3b21f;
    --paper: #ffffff;
    --paper-tint: #f3f4f6;
    --ink: #16305e;
    --backdrop: #e9e7e3;
  }
  * { box-sizing: border-box; margin: 0; padding: 0; }
  html, body { width: 1200px; height: 873px; overflow: hidden; }
  body {
    background: var(--backdrop);
    display: flex;
    align-items: center;
    justify-content: center;
    gap: 40px;
    font-family: "Open Sans", sans-serif;
  }
  .card {
    width: 540px;
    height: 309px;
    border-radius: 4px;
    overflow: hidden;
    box-shadow: 0 6px 18px rgba(20, 30, 60, 0.18);
    position: relative;
  }

  /* Front: name band + contact panel */
  .card-front { background: var(--paper); display: flex; flex-direction: column; }
  .name-band {
    height: 128px;
    background: linear-gradient(135deg, var(--navy-deep), var(--navy) 60%, #15408a);
    display: flex;
    flex-direction: column;
    align-items: center;
    justify-content: center;
    gap: 6px;
  }
  .person-name {
    font-family: "Montserrat", sans-serif;
    font-weight: 800;
    font-size: 58px;
    letter-spacing: 2px;
    color: var(--gold);
    line-height: 1;
  }
  .person-role {
    font-family: "Montserrat", sans-serif;
    font-weight: 600;
    font-size: 14px;
    letter-spacing: 1.5px;
    color: var(--gold);
  }
  .contact-panel {
    flex: 1;
    background: var(--paper-tint);
    display: grid;
    grid-template-columns: 1.15fr 1fr;
    gap: 14px 18px;
    padding: 22px 26px;
    align-content: center;
  }
  .contact-row { display: flex; align-items: center; gap: 10px; }
  .contact-icon {
    flex: 0 0 28px;
    width: 28px; height: 28px;
    border-radius: 50%;
    background: var(--navy);
    display: flex; align-items: center; justify-content: center;
  }
  .contact-icon svg { width: 16px; height: 16px; }
  .contact-text {
    font-size: 10.5px;
    line-height: 1.45;
    color: var(--ink);
    font-weight: 600;
  }

  /* Back: studio name + slogan */
  .card-back {
    background: var(--navy);
    display: flex;
    flex-direction: column;
    align-items: center;
    justify-content: center;
    gap: 14px;
  }
  .studio-name {
    font-family: "Montserrat", sans-serif;
    font-weight: 600;
    font-size: 28px;
    letter-spacing: 1px;
    color: var(--gold);
  }
  .slogan {
    font-family: "Montserrat", sans-serif;
    font-weight: 400;
    font-size: 15px;
    letter-spacing: 0.5px;
    color: var(--gold);
  }
</style>
</head>
<body>

  <section class="card card-front" aria-label="Business card front">
    <div class="name-band">
      <div class="person-name">NAME</div>
      <div class="person-role">PHOTOGRAPHER &amp; VEDIOGRAPHER</div>
    </div>
    <div class="contact-panel" role="img" aria-label="Contact details on a light background where a faint hexagon pattern belongs">
      <div class="contact-row">
        <span class="contact-icon">
          <svg viewBox="0 0 16 16"><path d="M8 1.5a4.5 4.5 0 0 0-4.5 4.5c0 3.4 4.5 8.5 4.5 8.5s4.5-5.1 4.5-8.5A4.5 4.5 0 0 0 8 1.5z" fill="#fff"/><circle cx="8" cy="6" r="1.7" fill="#0f3470"/></svg>
        </span>
        <p class="contact-text">57 tarrant street, glenmore nsw 2047</p>
      </div>
      <div class="contact-row">
        <span class="contact-icon">
          <svg viewBox="0 0 16 16"><path d="M4.2 1.8l2 3-1.3 1.3a8 8 0 0 0 4.9 4.9l1.3-1.3 3 2-1.2 2.2C7.7 13.7 2.3 8.3 2 3z" fill="#fff"/></svg>
        </span>
        <p class="contact-text">mobile: 0431872259<br>phone: (02) 9163 2408</p>
      </div>
      <div class="contact-row">
        <span class="contact-icon">
          <svg viewBox="0 0 16 16" fill="none" stroke="#fff" stroke-width="1.2"><circle cx="8" cy="8" r="6"/><ellipse cx="8" cy="8" rx="2.6" ry="6"/><path d="M2 8h12M3 5h10M3 11h10"/></svg>
        </span>
        <p class="contact-text">www.tidewillowstudio.net.au<br>facebook:tidewillowweddings<br>instagram:tidewillowweddings</p>
      </div>
      <div class="contact-row">
        <span class="contact-icon">
          <svg viewBox="0 0 16 16"><rect x="2" y="4" width="12" height="8.5" rx="1" fill="#fff"/><path d="M2.5 4.5L8 9l5.5-4.5" fill="none" stroke="#0f3470" stroke-width="1.2"/></svg>
        </span>
        <p class="contact-text">info@tidewillowstudio.net.au</p>
      </div>
    </div>
  </section>

  <section class="card card-back" role="img" aria-label="Business card back on navy where a faint hexagon pattern belongs">
    <div class="studio-name">golden hour studio and film</div>
    <div class="slogan">"love stories kept forever"</div>
  </section>

</body>
</html>
```